Varnik Holdings — Business Card Design Brief
Overview
Design a double-sided business card for Varnik Holdings that highlights our two service arms: Varnik Communications (telecommunications) and Varnik Energy (business energy solutions). The card should feel smart and stand out when handed to clients.

Objectives
Showcase our areas of specialty clearly.
Reflect the overall Varnik / Varnik Holdings brand while acknowledging both arms.
Explore using both logos (Communications + Energy) or one unified logo, depending on the design.

Deliverables
One double-sided business card design (front + back).

Content & Copy
Front (preferred): Logo: Varnik / Varnik Holdings
Descriptor: Business Communications | Business Energy
Back:My contact details and company details
Core products: Business Mobile • Telephony • Internet • Business Energy Solutions

Brand & Visual Direction
We have a group logo currently tailored more toward telecoms, plus a separate Varnik Energy logo.
Please explore layouts that use both logos or just one, whichever works best.
Color: I wouldn't mind seeing an option using our the Blue/Purple gradient from our website (varnik-example.co.uk), but also open to non-gradient approaches and other colours..

Overall look: Smart, modern, and distinctive.
Format & Print Specs
Double-sided business card format. (Use a standard size

Must-Haves
Front: Varnik wording or Varnik Holdings wording with atleast 1 logo also on front “Business Communications | Business Energy.”

Back: Contact + company details and core products.
A design that stands out while remaining professional.

Nice-to-Have Options
A gradient version using our site’s Blue/Purple gradient.
A non-gradient version.
A dual-logo treatment versus a single-logo treatment.

Thanks
Owen

```html
<!DOCTYPE html>
<html lang="en">
<head>
<meta charset="utf-8">
<title>Varnik Holdings — Business Card</title>
<link rel="stylesheet" href="https://fonts.googleapis.com/css2?family=Montserrat:wght@800&family=Roboto:wght@400;500;700&display=swap">
<style>
  :root {
    --backdrop: #e8e8e8;
    --navy: #1c1566;
    --ink-navy: #1c1a6b;
    --white: #ffffff;
    --green: #3cb521;
    --lime: #8dc21f;
    --sky: #1e90d6;
    --comms-blue: #1f6fd6;
    --rule: #6b6b6b;
  }
  * { box-sizing: border-box; margin: 0; padding: 0; }
  html, body {
    width: 1200px; height: 1200px; overflow: hidden;
    background: var(--backdrop);
    font-family: "Roboto", Arial, sans-serif;
  }
  .canvas { position: relative; width: 1200px; height: 1200px; }
  .card { position: absolute; width: 688px; height: 393px; }

  /* Contact side */
  .card--contact { left: 267px; top: 159px; background: var(--navy); color: var(--white); }
  .brand-name {
    position: absolute; left: 44px; top: 48px;
    font-family: "Montserrat", Arial, sans-serif; font-weight: 800;
    font-size: 56px; line-height: 1; letter-spacing: 0.5px; color: var(--white);
  }
  .person-name {
    position: absolute; left: 44px; top: 128px;
    font-weight: 700; font-size: 27px; line-height: 1; color: var(--green); letter-spacing: 0.3px;
  }
  .person-role {
    position: absolute; left: 44px; top: 158px;
    font-size: 16px; color: var(--sky);
  }
  .address {
    position: absolute; left: 44px; top: 198px;
    font-size: 17px; line-height: 21px; font-style: normal;
  }
  .contact-list {
    position: absolute; left: 44px; top: 252px; list-style: none;
    font-size: 17px; line-height: 20.5px;
  }
  .contact-list li { display: flex; align-items: center; gap: 12px; }
  .contact-list svg { width: 14px; height: 14px; flex: none; }
  .products {
    position: absolute; left: 46px; top: 351px;
    font-size: 17.5px; white-space: nowrap;
  }
  .products .dot { margin: 0 6px; }
  .brand-disc {
    position: absolute; left: 300px; top: 150px;
    width: 184px; height: 184px; border-radius: 50%;
    border: 14px solid var(--green);
    transform: translateX(0);
    left: 292px; top: 149px;
  }

  /* Brand side */
  .card--brands { left: 262px; top: 653px; background: var(--white); }
  .divider {
    position: absolute; left: 352px; top: 97px; width: 2px; height: 200px; background: var(--rule);
  }
  .arm { position: absolute; top: 80px; width: 300px; text-align: center; }
  .arm--comms { left: 52px; }
  .arm--energy { left: 340px; }
  .arm-disc {
    width: 96px; height: 96px; border-radius: 50%;
    margin: 0 auto 18px; border: 10px solid;
  }
  .arm--comms .arm-disc { border-color: var(--comms-blue); }
  .arm--energy .arm-disc { border-color: var(--green); }
  .arm-name {
    font-family: "Montserrat", Arial, sans-serif; font-weight: 800;
    font-size: 54px; line-height: 1; color: var(--ink-navy);
  }
  .arm-descriptor { margin-top: 14px; font-size: 17px; }
  .arm--comms .arm-descriptor { color: var(--comms-blue); }
  .arm--energy .arm-descriptor { color: var(--lime); letter-spacing: 3px; font-weight: 500; }
</style>
</head>
<body>
<main class="canvas">

  <section class="card card--contact" aria-label="Contact side">
    <h1 class="brand-name">VARNIK</h1>
    <p class="person-name">DANIEL REYES</p>
    <p class="person-role">President</p>
    <address class="address">412 Alder Row<br>Northfield 20831</address>
    <ul class="contact-list">
      <li>
        <svg viewBox="0 0 16 16" aria-hidden="true"><path fill="#3cb521" d="M3.6 1.2l2.3 2.6-1.3 1.8c.9 2 2.6 3.8 4.7 4.8l1.7-1.4 2.7 2.2-1.4 2.6C7.3 13.5 2.4 8.6 1 3.6z"/></svg>
        555-210-4471
      </li>
      <li>
        <svg viewBox="0 0 16 16" aria-hidden="true"><rect x="3.5" y="0.8" width="9" height="14.4" rx="1.6" fill="none" stroke="#3cb521" stroke-width="1.8"/><rect x="6.5" y="12" width="3" height="1.2" fill="#3cb521"/></svg>
        555-210-9382
      </li>
      <li>
        <svg viewBox="0 0 16 16" aria-hidden="true"><rect x="1" y="3" width="14" height="10" fill="#3cb521"/><path d="M1.5 3.5L8 9l6.5-5.5" fill="none" stroke="#1c1566" stroke-width="1.3"/></svg>
        info@varnik-example.co.uk
      </li>
      <li>
        <svg viewBox="0 0 16 16" aria-hidden="true"><circle cx="8" cy="8" r="7" fill="#3cb521"/><path d="M8 1v14M1 8h14M3 4.5h10M3 11.5h10" stroke="#1c1566" stroke-width="1" fill="none"/><ellipse cx="8" cy="8" rx="3.2" ry="7" fill="none" stroke="#1c1566" stroke-width="1"/></svg>
        www.varnik-example.co.uk
      </li>
    </ul>
    <div class="brand-disc" aria-hidden="true"></div>
    <p class="products">Business Mobile<span class="dot">•</span>Telephony<span class="dot">•</span>Internet<span class="dot">•</span>Business Energy Solutions</p>
  </section>

  <section class="card card--brands" aria-label="Brand side">
    <div class="arm arm--comms">
      <div class="arm-disc" aria-hidden="true"></div>
      <p class="arm-name">VARNIK</p>
      <p class="arm-descriptor">BUSINESS COMMUNICATIONS</p>
    </div>
    <div class="divider" aria-hidden="true"></div>
    <div class="arm arm--energy">
      <div class="arm-disc" aria-hidden="true"></div>
      <p class="arm-name">VARNIK</p>
      <p class="arm-descriptor">BUSINESS ENERGY</p>
    </div>
  </section>

</main>
</body>
</html>
```